Need a new company business card

I am looking for a new company business card. Front and back. With information on it as per below. Card should be professional. Yet clever. Simple. Modern design. Pim card, traditional size. OK with say, all black or all red backside.

Varnholt is an indie, bootstrapped magazine advancing the work of intersectional feminists busting their buts to create a just world through the power of enterprise and innovation.

Varnholt is the home and voice of entrepreneurial feminism and feminist innovators worldwide. Entrepreneurial feminists are people (of all genders) who see inequality as an innovation priority. They work to advance gender equity and/or who strive to integrate and practice feminist principles, pedagogy, values into their innovation and entrepreneurship work.
We are committed to this space being trans and queer inclusive, anti-racist, intersectional, brave, and safe. We welcome all allies. We value learning, edgy but civil discourse and integrative thinking skills.

Target Market(s)

feminists, business owners,

Industry/Entity Type

Publishing Company

Contact Information for Business Card

RD Tolliver
Founder/Publisher
4-237 Ashgrove Lane, Toronto, ON
M4T 2K8
publisher@varnholt.com
416-552-3019
www.varnholt.com

Font styles to use
Serif
Other font styles liked:
• Myriad Pro

Colors
ec1f27
000000
ffffff

Requirements
Must have
• logo
• use red, black white colours only.
Nice to have
• use the compass in pattern or creatively but not too busy please
Should not have
• Should not be too busy. Elegant.

```html
<!DOCTYPE html>
<html lang="en">
<head>
<meta charset="utf-8">
<title>Varnholt Business Card</title>
<link rel="stylesheet" href="https://fonts.googleapis.com/css2?family=Roboto:wght@400;500;700&display=swap">
<style>
  :root {
    --stage: #a9a9a9;
    --ink: #2b2b2b;
    --card-white: #ffffff;
    --card-black: #1c1c1c;
    --brand-red: #ec1f27;
  }
  * { margin: 0; padding: 0; box-sizing: border-box; }
  html, body {
    width: 1200px; height: 1138px; overflow: hidden;
    background: var(--stage);
    font-family: "Roboto", Arial, sans-serif;
  }
  .canvas { position: relative; width: 1200px; height: 1138px; }
  .card {
    position: absolute;
    width: 620px; height: 374px;
    border-radius: 12px;
    overflow: hidden;
  }
  .card-front {
    left: 274px; top: 186px;
    background: var(--card-black);
  }
  .front-artwork {
    position: absolute; inset: 0;
    background: radial-gradient(ellipse at 35% 50%, #2a2a2a 0%, var(--card-black) 70%);
  }
  .front-brand {
    position: absolute; left: 420px; top: 150px; width: 150px;
    text-align: center;
    font-weight: 700; font-size: 28px; color: var(--brand-red);
  }
  .card-back {
    left: 276px; top: 608px;
    background: var(--card-white);
  }
  .back-brand {
    position: absolute; right: 40px; top: 64px;
    font-weight: 700; font-size: 30px; color: var(--brand-red);
  }
  .holder-name {
    position: absolute; left: 34px; top: 222px;
    font-weight: 700; font-size: 22px; color: var(--ink);
  }
  .holder-title {
    position: absolute; left: 34px; top: 253px;
    font-size: 14px; color: var(--ink);
  }
  .divider {
    position: absolute; left: 34px; top: 284px;
    width: 549px; height: 2px; background: var(--brand-red);
  }
  .contact-row {
    position: absolute; left: 34px;
    display: flex; align-items: center; gap: 12px;
    font-size: 14px; color: var(--ink);
  }
  .contact-row.primary { top: 297px; }
  .contact-row.address { top: 325px; }
  .contact-item { display: flex; align-items: center; gap: 10px; }
  .contact-item svg { width: 14px; height: 14px; fill: var(--brand-red); flex: none; }
</style>
</head>
<body>
<div class="canvas">
  <section class="card card-front">
    <div class="front-artwork" role="img" aria-label="Hand-drawn white line illustration on black of a woman's portrait beside a speech bubble, surrounded by a crowd of sketched faces, hearts and raindrops"></div>
    <div class="front-brand">Varnholt</div>
  </section>

  <section class="card card-back">
    <div class="back-brand">Varnholt</div>
    <div class="holder-name">RD Tolliver</div>
    <div class="holder-title">Founder/Publisher</div>
    <div class="divider"></div>
    <div class="contact-row primary">
      <span class="contact-item">
        <svg viewBox="0 0 24 24"><path d="M6.6 10.8a15 15 0 0 0 6.6 6.6l2.2-2.2a1 1 0 0 1 1-.25 11.4 11.4 0 0 0 3.6.57 1 1 0 0 1 1 1V20a1 1 0 0 1-1 1A17 17 0 0 1 3 4a1 1 0 0 1 1-1h3.5a1 1 0 0 1 1 1c0 1.25.2 2.45.57 3.57a1 1 0 0 1-.25 1z"/></svg>
        416-552-3019
      </span>
      <span class="contact-item">
        <svg viewBox="0 0 24 24"><path d="M2 5h20v14H2z M3.5 6.5 12 13l8.5-6.5" stroke="#fff" stroke-width="1.5"/></svg>
        publisher@varnholt.com
      </span>
      <span class="contact-item">
        <svg viewBox="0 0 24 24"><circle cx="12" cy="12" r="10"/><path d="M2 12h20M12 2c3 3 3 17 0 20M12 2c-3 3-3 17 0 20" stroke="#fff" stroke-width="1.5" fill="none"/></svg>
        www.varnholt.com
      </span>
    </div>
    <div class="contact-row address">
      <span class="contact-item">
        <svg viewBox="0 0 24 24"><path d="M12 2a7 7 0 0 0-7 7c0 5 7 13 7 13s7-8 7-13a7 7 0 0 0-7-7zm0 9.5A2.5 2.5 0 1 1 12 6.5a2.5 2.5 0 0 1 0 5z"/></svg>
        4-237 Ashgrove Lane, Toronto, ON M4T 2K8
      </span>
    </div>
  </section>
</div>
</body>
</html>
```